Landing Page für Freelancer im Bereich der Informationstechnik
Zielgruppe
Ich bin Experte für Informationstechnik, Unified Communications, Beratung, Management sowie Projekte aller Art.
Mit meiner WELLENBERG GmbH bin ich als (einzelner) Freelancer für mittelständische Unternehmen und Konzerne in verschiedensten Projekten tätig.
Mein Motto lautet 'Mit Präzision und langjähriger Erfahrung immer alles im Griff!'
Aufgabenstellung
Die aktuell existierende Internet-Präsenz unter wellenberg-beispiel.de beinhaltet aktuell nur eine minimalistische statische Seite sowie das Impressum, ohne jegliche dynamische Inhalte.
DABEI SOLL ES BLEIBEN. Auch die Inhalte sollen unverändert übernommen werden.
Lediglich soll jetzt eine Anlehnung an das zwischenzeitlich vorhandene Logo vorgenommen werden, welches ich mitliefere.
Es geht mir insgesamt nur darum, ein professionelleres Auftreten zu haben, WENN sich denn mal jemand auf die Seite verirrt.
Das Aussehen soll daher modern und dynamisch sein.
ZUSAMMENFASSUNG: Inhalte bleiben 1:1, grafische Anpassung an Logo gewünscht.
Technisch: Statisch, kein Content-Management. Lohnt sich hier nicht.
SEHR WICHTIG: Ich möchte gerne, dass die Lieferung bereits als HTML (und NICHT NUR ALS GRAFIK) erfolgt, ggf. stelle ich auch kurz den FTP-Zugang.
Insgesamt möchte ich gar keine große Sache draus machen.
Viele Anpassungsrunden wird es voraussichtlich nicht geben.
Zeitlich ist dies hier ein sehr kleines Projekt - Erweiterungen kommen später.

```html
<!DOCTYPE html>
<html lang="de">
<head>
<meta charset="utf-8">
<title>Lukas Martin Brenner – WELLENBERG GmbH</title>
<link href="https://fonts.googleapis.com/css2?family=Nunito:wght@600;700&display=swap" rel="stylesheet">
<style>
  :root {
    --ink: #454545;
    --accent: #4aa3bf;
    --paper: #ffffff;
    --hero-left: #d9d9e6;
    --hero-right: #a9bed8;
    --hero-mid: #c9d4e4;
  }
  * { margin: 0; padding: 0; box-sizing: border-box; }
  html, body { width: 1200px; height: 675px; overflow: hidden; background: var(--paper); }
  body { font-family: "Nunito", sans-serif; color: var(--ink); font-weight: 700; position: relative; }

  .hero {
    position: absolute; left: 0; top: 0; width: 1200px; height: 303px;
    background: linear-gradient(100deg, var(--hero-left) 0%, var(--hero-mid) 45%, var(--hero-right) 100%);
  }
  .hero-panel {
    position: absolute; left: 237px; top: 0; width: 338px; height: 303px;
    background: rgba(250, 251, 253, 0.93);
    text-align: center;
  }
  .brand {
    position: absolute; left: 0; right: 0; top: 112px;
    display: flex; align-items: center; justify-content: center; gap: 7px;
    color: var(--accent); font-size: 15px; letter-spacing: 1.5px;
  }
  .brand-dot { width: 9px; height: 9px; border-radius: 50%; background: var(--accent); }
  .motto {
    position: absolute; left: 0; right: 0; top: 186px;
    font-size: 12.6px; line-height: 18.5px; text-transform: uppercase;
  }

  .intro { position: absolute; left: 237px; top: 352px; }
  .degree { font-size: 13px; }
  .name { color: var(--accent); font-size: 27.5px; font-weight: 600; margin-top: 10px; line-height: 1.1; }
  .master { font-size: 13px; margin-top: 10px; }

  .offer { position: absolute; left: 625px; top: 354px; width: 340px; }
  .email {
    display: inline-block; font-size: 9px; color: var(--ink); text-decoration: none;
    padding-bottom: 3px; border-bottom: 1px solid var(--ink);
  }
  .services { font-size: 18px; line-height: 23.5px; margin-top: 10px; }
  .note { font-size: 8.6px; line-height: 14.4px; margin-top: 11px; }

  .divider { position: absolute; left: 237px; top: 527px; width: 726px; height: 1px; background: var(--accent); }
  .footer-nav { position: absolute; left: 237px; top: 548px; display: flex; gap: 32px; font-size: 10.6px; }
  .footer-nav a { color: var(--ink); text-decoration: none; }
</style>
</head>
<body>
  <header class="hero" role="img" aria-label="Illustration eines Schreibtischs von oben mit Laptop, Monitor, Tastatur, Kaffeetasse und Notizbuch">
    <div class="hero-panel">
      <div class="brand"><span class="brand-dot"></span><span>WELLENBERG GmbH</span></div>
      <p class="motto">"Mit Präzision und<br>langjähriger Erfahrung immer<br>alles im Griff!"</p>
    </div>
  </header>

  <section class="intro">
    <p class="degree">Diplom-Informatiker (FH)</p>
    <h1 class="name">Lukas Martin Brenner</h1>
    <p class="master">Master of Science in Electronic Business</p>
  </section>

  <section class="offer">
    <a class="email" href="#">l punkt brenner at wellenberg-beispiel punkt de</a>
    <h2 class="services">Experte für Informationstechnik | Unified Communications | Beratung | Management | Projekte aller Art</h2>
    <p class="note">Gerne schicke ich Ihnen unverbindlich mein Expertenprofil samt CV sowie meine aktuellen Verfügbarkeiten zu. Kontaktieren Sie mich hierzu einfach per E-Mail unter l punkt brenner at wellenberg-beispiel punkt de. Ich freue mich auf Sie!</p>
  </section>

  <div class="divider"></div>
  <nav class="footer-nav">
    <a href="#">Startseite</a>
    <a href="#">Impressum</a>
    <a href="#">Datenschutz</a>
  </nav>
</body>
</html>
```